New Business Card Design for Manufacturing

We are an engineering/manufacturing company that offers Advanced machining/assembly/engineering services, as well as innovative products for the heavy duty engine cooling markets.

We are looking to get a new business card designed that is clean and modern looking, but still fits the wide range of technical/skilled work we do.

- We hope to use this design as the base for other design work in new Presentations, web, and print work.

Industry/Entity Type

Engineering

Contact Information for Business Card

Our preferred color of blue is (RGB) 22/71/159 but can vary slightly from that color. Our content will be our Logo and full company name (Vantrell Forge Works, Inc.), company address, name, job title, phone number with extension, cell number, fax number, website, and email address on the cards.
We'd like the full company name next to the logo, but we are open to other interpretations of that layout.
Preferably, we would like the back side to be clean with just our logo, and the front to contain all of the contact information.

Colors
2f74b4
0355a3
85abd2

Requirements
Must have
• - Logo, company name, needed content - We are open to interpretation beyond that.
• - Standard size business card.
• - Horizontal orientation.
• - Enough space for lengthy names / job titles (for example, a job title could read "Directory of Human Resources" or "V.P. of Governmental Affairs"). We need this to look clean, whether the title be short (CEO) or long (as described above).

```html
<!DOCTYPE html>
<html lang="en">
<head>
<meta charset="utf-8">
<title>Vantrell Forge Works – Business Card</title>
<link href="https://fonts.googleapis.com/css2?family=Fira+Sans:wght@400;500;800&display=swap" rel="stylesheet">
<style>
  :root {
    --brand-blue: #0355a3;
    --ink-light: #ffffff;
    --ink-soft: #e3ecf6;
    --backdrop: #e6e6e6;
    --card-white: #f7f7f7;
    --card-white-edge: #e8e8e8;
  }
  * { box-sizing: border-box; margin: 0; padding: 0; }
  html, body {
    width: 1200px; height: 576px; overflow: hidden;
    background: var(--backdrop);
    font-family: "Fira Sans", Arial, sans-serif;
  }
  .stage { position: relative; width: 1200px; height: 576px; }
  .card {
    position: absolute; top: 138px; width: 484px; height: 294px;
    border-radius: 14px; overflow: hidden;
    box-shadow: 0 3px 6px rgba(0,0,0,.22);
  }
  .wordmark { font-weight: 800; letter-spacing: 1px; line-height: 1; }

  /* Back side */
  .card--back { left: 82px; background: var(--brand-blue); color: var(--ink-light); }
  .back-lockup { position: absolute; left: 0; right: 0; top: 102px; text-align: center; }
  .card--back .wordmark { font-size: 66px; }
  .back-web {
    position: absolute; left: 0; right: 0; top: 266px;
    display: flex; justify-content: center; align-items: center; gap: 12px;
    font-size: 13px; color: var(--ink-soft);
  }
  .back-web .rule { width: 52px; height: 2px; background: var(--ink-soft); border-radius: 1px; }

  /* Front side */
  .card--front {
    left: 602px;
    background: linear-gradient(135deg, var(--card-white), var(--card-white-edge));
  }
  .front-band { position: absolute; inset: 0; }
  .person { position: absolute; left: 26px; top: 28px; color: var(--ink-light); }
  .person-name { font-size: 19px; font-weight: 500; }
  .person-title { font-size: 11px; margin-top: 2px; color: var(--ink-soft); }
  .contact { position: absolute; left: 26px; top: 130px; color: var(--ink-light); }
  .company-name { font-size: 12.5px; font-weight: 500; margin-bottom: 7px; }
  .contact-list { list-style: none; font-size: 11.5px; }
  .contact-list li { display: flex; align-items: center; height: 16px; gap: 8px; }
  .contact-list svg { width: 10px; height: 10px; fill: var(--ink-light); flex: none; }
  .address { font-size: 11.5px; line-height: 15.5px; margin-top: 9px; }
  .front-lockup { position: absolute; left: 276px; top: 218px; width: 188px; text-align: center; }
  .card--front .wordmark { font-size: 38px; color: var(--brand-blue); }
</style>
</head>
<body>
<main class="stage">
  <section class="card card--back" aria-label="Card back">
    <div class="back-lockup">
      <div class="wordmark">VANTRELL</div>
    </div>
    <div class="back-web"><span class="rule"></span>www.vantrellforge.com<span class="rule"></span></div>
  </section>

  <section class="card card--front" aria-label="Card front">
    <svg class="front-band" viewBox="0 0 484 294" preserveAspectRatio="none" aria-hidden="true">
      <polygon points="0,0 316,0 244,294 0,294" fill="var(--brand-blue)"/>
    </svg>
    <div class="person">
      <div class="person-name">Marcus Ellory Hale</div>
      <div class="person-title">Managing Director</div>
    </div>
    <div class="contact">
      <div class="company-name">Vantrell Forge Works, Inc.</div>
      <ul class="contact-list">
        <li><svg viewBox="0 0 10 10"><path d="M1 3c0-1.5 1.5-2 4-2s4 .5 4 2v1H7V3H3v1H1zM2 5h6l1 4H1z"/></svg>555-0142-2210 (ext. 214)</li>
        <li><svg viewBox="0 0 10 10"><path d="M3 0h4a1 1 0 0 1 1 1v8a1 1 0 0 1-1 1H3a1 1 0 0 1-1-1V1a1 1 0 0 1 1-1zm0 1.5v6h4v-6z"/></svg>555-0187-3391</li>
        <li><svg viewBox="0 0 10 10"><path d="M3 0h4v3H3zM0 3.5h10v4H8V10H2V7.5H0zM3 6v3h4V6z"/></svg>555-0163-4470</li>
        <li><svg viewBox="0 0 10 10"><path d="M0 2h10v6H0zM1 3l4 3 4-3v-.3H1z"/></svg>www.vantrellforge.com</li>
        <li><svg viewBox="0 0 10 10"><path d="M5 0a5 5 0 1 0 0 10A5 5 0 0 0 5 0zm-.6 1.2C3.6 2.3 3.3 3.6 3.2 4.5H1.2a3.9 3.9 0 0 1 3.2-3.3zm1.2 0a3.9 3.9 0 0 1 3.2 3.3H6.8c-.1-.9-.4-2.200-1.2-3.3zM4.2 4.5C4.3 3.4 4.6 2.3 5 1.6c.4.7.7 1.8.8 2.900zm-3 1h2c.1.9.4 2.2 1.2 3.3A3.9 3.9 0 0 1 1.2 5.5zm3 0h1.6c-.1 1.1-.4 2.2-.8 2.9-.4-.7-.7-1.8-.8-2.9zm2.6 0h2a3.9 3.9 0 0 1-3.2 3.3c.8-1.1 1.1-2.4 1.2-3.3z"/></svg>mhale@vantrellforge.com</li>
      </ul>
      <p class="address">418 Millrace Rd., Harlow Falls,<br>Brenton, US 604127</p>
    </div>
    <div class="front-lockup">
      <div class="wordmark">VANTRELL</div>
    </div>
  </section>
</main>
</body>
</html>
```